Ward Compass Business Card Design*

We need a business card design for our company Ward Compass. Our company is specialized in providing online consulting services regarding medical institutions, hospitals and doctors. We work with patients worldwide looking to choose between healthcare providers. We have a website you may use as a reference, where we list doctors and clinics worldwide. So we target Medical providers as well as patients worldwide.
Target Market(s)
Medical Providers and patients around the world
Industry/Entity Type
Medical
Contact Information for Business Card
Salwa Kettani
CEO
+90 612 348 2175
info@wardcompass.example
www.wardcompass.example
14 Annakhil 7 H.R.B. Rabat, Morocco
Requirements
Must have
- Company logo/name on one full side, personal info and smaller logo and company name on the other side.
Nice to have
- Smart and elegant design

```html
<!DOCTYPE html>
<html lang="en">
<head>
<meta charset="utf-8">
<title>Ward Compass — Business Card</title>
<link rel="stylesheet" href="https://fonts.googleapis.com/css2?family=Montserrat:wght@300;400;600;700&display=swap">
<style>
  :root {
    --navy: #1b4674;
    --slate: #7d7a7a;
    --paper: #f3f3f4;
    --white: #ffffff;
    --backdrop: #e7e4df;
    --card-shadow: 0 4px 10px rgba(0, 0, 0, 0.35);
  }
  * { margin: 0; padding: 0; box-sizing: border-box; }
  html, body {
    width: 900px;
    height: 1200px;
    overflow: hidden;
    background: var(--backdrop);
    font-family: "Montserrat", "Helvetica Neue", Arial, sans-serif;
  }
  .canvas { position: relative; width: 900px; height: 1200px; }
  .card {
    position: absolute;
    left: 77px;
    width: 746px;
    height: 436px;
    background: var(--navy);
    box-shadow: var(--card-shadow);
    overflow: hidden;
  }
  .card--front { top: 134px; }
  .card--back { top: 637px; }

  /* Front */
  .brand {
    position: absolute;
    top: 190px;
    left: 0;
    width: 100%;
    display: flex;
    align-items: center;
    justify-content: center;
    gap: 22px;
  }
  .brand__dot {
    width: 58px;
    height: 58px;
    border-radius: 50%;
    background: var(--slate);
  }
  .brand__name {
    color: var(--white);
    font-weight: 600;
    font-size: 44px;
    letter-spacing: 1px;
    text-transform: uppercase;
    line-height: 1;
  }
  .website {
    position: absolute;
    top: 428px;
    left: 0;
    width: 100%;
    text-align: center;
    color: var(--white);
    font-size: 16px;
    font-weight: 400;
  }
  .card--front .website { top: 394px; }

  /* Back */
  .back-shape { position: absolute; inset: 0; }
  .person { position: absolute; left: 44px; top: 96px; color: var(--white); }
  .person__name { font-size: 25px; font-weight: 400; text-transform: uppercase; letter-spacing: 0.3px; }
  .person__name strong { font-weight: 700; }
  .person__role { font-size: 17px; font-weight: 300; margin-top: 2px; }
  .contacts { position: absolute; left: 44px; top: 346px; list-style: none; color: var(--white); }
  .contacts li {
    display: flex;
    align-items: center;
    gap: 20px;
    font-size: 17px;
    font-weight: 300;
    height: 26px;
  }
  .contacts svg { width: 19px; height: 19px; flex: none; }
  .emblem {
    position: absolute;
    left: 490px;
    top: 108px;
    width: 230px;
    display: flex;
    flex-direction: column;
    align-items: center;
    gap: 20px;
  }
  .emblem__dot {
    width: 150px;
    height: 150px;
    border-radius: 50%;
    background: var(--navy);
  }
  .emblem__name {
    color: var(--navy);
    font-weight: 600;
    font-size: 20px;
    letter-spacing: 1px;
    text-transform: uppercase;
  }
</style>
</head>
<body>
<main class="canvas">
  <section class="card card--front" aria-label="Card front">
    <div class="brand">
      <span class="brand__dot" aria-hidden="true"></span>
      <span class="brand__name">Ward Compass</span>
    </div>
    <p class="website">www.wardcompass.example</p>
  </section>

  <section class="card card--back" aria-label="Card back">
    <svg class="back-shape" viewBox="0 0 746 436" width="746" height="436" aria-hidden="true">
      <path d="M484 0 C360 70 330 330 458 436 L746 436 L746 0 Z" fill="var(--slate)"/>
      <path d="M498 0 C390 70 370 330 470 436 L746 436 L746 0 Z" fill="var(--paper)"/>
    </svg>

    <div class="person">
      <p class="person__name"><strong>Salwa</strong> Kettani</p>
      <p class="person__role">CEO</p>
    </div>

    <ul class="contacts">
      <li>
        <svg viewBox="0 0 20 20" aria-hidden="true">
          <circle cx="10" cy="10" r="10" fill="var(--white)"/>
          <path d="M7 5.2c.4-.3.9-.2 1.1.2l1 1.7c.2.4.1.8-.2 1.1l-.7.6c.5 1.1 1.3 1.9 2.4 2.4l.6-.7c.3-.3.7-.4 1.1-.2l1.7 1c.4.2.5.7.2 1.1l-.7.9c-.4.5-1.1.7-1.7.5-2.9-1-5-3.1-6-6-.2-.6 0-1.3.5-1.7z" fill="var(--navy)"/>
        </svg>
        <span>+90 612 348 2175</span>
      </li>
      <li>
        <svg viewBox="0 0 20 20" aria-hidden="true">
          <circle cx="10" cy="10" r="10" fill="var(--white)"/>
          <rect x="5" y="6.5" width="10" height="7" rx="1" fill="var(--navy)"/>
          <path d="M5.5 7.2 10 10.6l4.5-3.4" fill="none" stroke="var(--white)" stroke-width="0.9"/>
        </svg>
        <span>info@wardcompass.example</span>
      </li>
    </ul>

    <div class="emblem">
      <span class="emblem__dot" aria-hidden="true"></span>
      <span class="emblem__name">Ward Compass</span>
    </div>
  </section>
</main>
</body>
</html>
```